Rollers & Glides.com

Vertical Business Card with focus on branding with our icon. Information on card will be logo, persons name, position, phone number, email address and website. Use the the name Marcus Pellow, position President, phone number 480.915.2267, email Marcus@rollersandglides-demo.com, website www.rollersandglides-demo.com.

```html
<!DOCTYPE html>
<html lang="en">
<head>
<meta charset="utf-8">
<title>Rollers &amp; Glides.com — Business Card</title>
<link rel="stylesheet" href="https://fonts.googleapis.com/css2?family=Roboto:wght@500;700&family=Arimo:wght@400;700&display=swap">
<style>
  :root {
    --brand-blue: #3560ad;
    --card-white: #ffffff;
    --ink: #1c1c1c;
    --divider: #b9bcc2;
    --backdrop: #2a2a2a;
  }
  * { box-sizing: border-box; margin: 0; padding: 0; }
  html, body {
    width: 1200px; height: 1015px; overflow: hidden;
    background: var(--backdrop);
  }
  .canvas {
    position: relative; width: 1200px; height: 1015px;
  }
  .card {
    position: absolute; left: 250px; width: 700px; height: 400px;
    box-shadow: 0 18px 40px rgba(0,0,0,.55);
    overflow: hidden;
  }
  /* Front */
  .card--front { top: 70px; background: var(--brand-blue); }
  .front-mark {
    position: absolute; left: 70px; top: 120px;
    width: 160px; height: 160px; border-radius: 50%;
    background: var(--card-white);
  }
  .front-name {
    position: absolute; left: 270px; top: 178px;
    font-family: "Roboto", sans-serif; font-weight: 500;
    font-size: 36px; letter-spacing: 2.5px; color: var(--card-white);
  }
  /* Back */
  .card--back { top: 535px; background: var(--card-white); }
  .back-brand {
    position: absolute; left: 40px; top: 0; width: 300px; height: 386px;
    display: flex; flex-direction: column; align-items: center; justify-content: center; gap: 20px;
  }
  .back-mark {
    width: 70px; height: 70px; border-radius: 50%; background: var(--brand-blue);
  }
  .back-name {
    font-family: "Roboto", sans-serif; font-weight: 500;
    font-size: 25px; letter-spacing: 1.8px; color: var(--brand-blue);
  }
  .divider {
    position: absolute; left: 360px; top: 95px; width: 1px; height: 200px;
    background: var(--divider);
  }
  .contact {
    position: absolute; left: 392px; top: 108px;
    font-family: "Arimo", sans-serif; color: var(--ink);
  }
  .contact-name {
    font-weight: 700; font-size: 24px; color: var(--brand-blue); letter-spacing: .3px;
  }
  .contact-role { font-size: 18px; margin-top: 2px; }
  .contact-list { list-style: none; margin-top: 26px; }
  .contact-list li {
    display: flex; align-items: center; gap: 10px; font-size: 15.5px; line-height: 26px;
  }
  .contact-list svg { width: 16px; height: 16px; fill: var(--brand-blue); flex: none; }
  .web-domain { color: var(--brand-blue); }
  .bottom-band {
    position: absolute; left: 0; bottom: 0; width: 100%; height: 14px;
    background: var(--brand-blue);
  }
</style>
</head>
<body>
<main class="canvas">
  <section class="card card--front">
    <div class="front-mark"></div>
    <p class="front-name">Rollers &amp; Glides.com</p>
  </section>

  <section class="card card--back">
    <div class="back-brand">
      <div class="back-mark"></div>
      <p class="back-name">Rollers &amp; Glides.com</p>
    </div>
    <div class="divider"></div>
    <div class="contact">
      <h1 class="contact-name">MARCUS PELLOW</h1>
      <p class="contact-role">President</p>
      <ul class="contact-list">
        <li>
          <svg viewBox="0 0 16 16" aria-hidden="true"><path d="M3.5 1.5l2.6 2.6-1.5 1.8c.9 2 2.5 3.6 4.5 4.5l1.8-1.5 2.6 2.6-1.7 2.4C7 13.5 2.5 9 1.1 3.2z"/></svg>
          480.915.2267
        </li>
        <li>
          <svg viewBox="0 0 16 16" aria-hidden="true"><path d="M1 3h14v1.2L8 9 1 4.2zM1 5.8l7 4.8 7-4.8V13H1z"/></svg>
          Marcus@rollersandglides-demo.com
        </li>
        <li>
          <svg viewBox="0 0 16 16" aria-hidden="true"><path d="M8 1a7 7 0 1 0 0 14A7 7 0 0 0 8 1zm0 1.5c.8 0 1.7 1.5 2 3.8H6c.3-2.3 1.2-3.8 2-3.8zM2.6 7.3h2.3v1.4H2.6zm3.3 0h4.2v1.4H5.9zm5.2 0h2.3v1.4h-2.3zM6 9.7h4c-.3 2.3-1.2 3.8-2 3.8s-1.7-1.5-2-3.8z"/></svg>
          <span>www.<span class="web-domain">rollersandglides-demo</span>.com</span>
        </li>
      </ul>
    </div>
    <div class="bottom-band"></div>
  </section>
</main>
</body>
</html>
```